International Petrochemical business needs a web design for Clearway Desk system

We need a web design for a "Clearway Desk" system for an international petrochemical company. The web site is used internally within the company. It is hosted by an internal department which provides government permit request service for other departments.

We would like to see designs of two pages using color light blue. (home page, internal page as attached).
Home Page:
1. Header has a background image and small animation. Header on home page can be taller than the header of the internal page.
2. Layout as attached.

Internal Page:
1. Header can use the same background image as the home page and can be shorter to utilize the page for content.
2. The blue icon behind every captions represent an icon. When user move mouse over this icon, it displays the caption in Thai language as a tooltip. This icon needs to be redesign.

The final design should communicate the followings:
- Excellent service provided system in terms of time and accurary
- Rapid growth of business via building petrochemical refinery plant
Updates

For Internal Page, the blue circle behind every captions represent an icon. When mouse over this icon, a tool tip showing the caption in Thai language is shown. Please also design this icon..

There are more feedbacks from customer as followed:

1. Banner should consists of 
    1.1 "Approved" stamp on paper
    1.2 An image of Garuda. It is used on every government documents in Thailand
    1.3 Image of petrochemical plant
2. Each menu item (Home, Permit, Search, etc) should have different colors. Drop down menu will use the same color as its parent menu item.
3. Overall tone of the web page should be light blue with background of the body the web page in white
4. "New Request" button should use green color with icon on it
5. Table header of each box in the body of the page should use dark blue background with text in white

Please kindly submit your revisions.
Thank you.

Industry/Entity Type

Business

Requirements
Must have
• 1. Design for 1024x768 screen resolution
2. Use light blue theme
3. Background of header where the company logo is must have white background

```html
<!DOCTYPE html>
<html lang="en">
<head>
<meta charset="utf-8">
<title>Clearway Desk – Request Form</title>
<link href="https://fonts.googleapis.com/css2?family=Titillium+Web:wght@400;600;700&family=Sarabun:wght@500&display=swap" rel="stylesheet">
<style>
:root{
  --page-bg:#eef2f9;
  --navy:#1d3f73;
  --panel:#234b86;
  --cyan:#2aa7e0;
  --shadow-blue:#1b7fd0;
  --field-border:#bcbcbc;
  --field-text:#666;
  --label:#222;
  --tag-bg:#d6d6d6;
  --table-head:#1aa3e6;
  --table-foot:#7f9cbb;
  --nav-home:#1da1e2;--nav-permits:#f4a21a;--nav-search:#6cb52d;
  --nav-report:#e0393e;--nav-admin:#8b5aa8;--nav-help:#6a7a9a;
  --req:#e0393e;
}
*{box-sizing:border-box;margin:0;padding:0}
html,body{width:968px;height:1200px;overflow:hidden;background:var(--page-bg)}
body{font-family:"Titillium Web",sans-serif;color:var(--label)}
.stage{position:absolute;left:0;top:0;width:1200px;height:1487px;transform:scale(.80667);transform-origin:0 0}
.abs{position:absolute}
.sheet-shadow{left:128px;top:32px;width:988px;height:1378px;background:var(--shadow-blue)}
.sheet-grey{left:122px;top:26px;width:988px;height:1374px;background:#c9d0da}
.sheet{left:117px;top:20px;width:985px;height:1372px;background:#fff;border:1px solid var(--cyan)}
.brand{left:172px;top:52px;display:flex;align-items:center;gap:8px;font-weight:700;font-size:20px;color:var(--cyan)}
.brand-dot{width:36px;height:36px;border-radius:50%;background:var(--cyan)}
.site-title{right:124px;top:40px;font-size:27px;font-weight:700;color:var(--navy);letter-spacing:.5px}
.nav{left:675px;top:88px;width:403px;display:flex;font-size:12.5px;font-weight:600;color:var(--navy)}
.nav a{text-decoration:none;color:inherit;text-align:center;padding-bottom:5px;border-bottom:3px solid}
.banner{left:141px;top:126px;width:939px;height:152px;background:linear-gradient(90deg,#6b7a90 0%,#2f4266 30%,#1e2d4a 60%,#4d5f7c 100%)}
.panel-head{left:140px;top:310px;width:942px;height:43px;background:var(--panel);color:#fff;font-size:18px;font-weight:700;padding:8px 15px;letter-spacing:.3px}
.panel-body{left:140px;top:353px;width:942px;height:1019px;border:1px solid var(--panel);border-top:none}
.row{position:absolute;height:34px}
.lbl{position:absolute;right:0;line-height:34px;font-size:15px;font-weight:600;white-space:nowrap}
.req{color:var(--req);font-size:10px;vertical-align:top;margin-left:1px;line-height:26px}
.ico{position:absolute;width:34px;height:34px}
.colon{position:absolute;width:6px;font-weight:700;line-height:34px;font-size:15px}
.field{position:absolute;height:27px;border:1px solid var(--field-border);border-radius:4px;background:linear-gradient(#f2f2f2,#fff 45%);color:var(--field-text);font-size:14.5px;padding:0 10px;line-height:25px;white-space:nowrap}
.field.area{height:90px;line-height:20px;padding-top:6px}
.caret{position:absolute;right:6px;top:8px;width:0;height:0;border-left:6px solid transparent;border-right:6px solid transparent;border-top:11px solid #777}
.btn{position:absolute;height:25px;border:1px solid #b5b5b5;border-radius:4px;background:linear-gradient(#fafafa,#d8d8d8);color:#777;font-size:13px;text-align:center;line-height:23px;letter-spacing:.5px}
.tag{position:absolute;height:17px;background:var(--tag-bg);border:1px solid #b9b9b9;border-radius:2px;font-size:10.5px;color:#777;line-height:15px;padding-left:5px}
.tag b{position:absolute;right:0;top:-1px;width:22px;height:17px;border:1px solid #b9b9b9;background:#eee;text-align:center;font-weight:600;color:#666}
.tooltip{left:696px;top:448px;width:164px;height:46px;background:var(--navy);color:#fff;font-family:"Sarabun",sans-serif;font-size:11px;line-height:15px;padding:7px 12px;border-radius:3px}
.tooltip:before{content:"";position:absolute;left:120px;top:-8px;border-left:8px solid transparent;border-right:8px solid transparent;border-bottom:8px solid var(--navy)}
.related{left:366px;top:1153px;width:399px;height:153px;border:1px solid #a9c4dc;border-collapse:collapse;font-size:12px}
.related th{background:var(--table-head);color:var(--navy);font-size:14px;font-weight:600;text-align:left;height:28px;padding-left:12px;border-right:1px solid #fff}
.related td{vertical-align:top;padding:10px 0 8px 12px;line-height:18px;border-right:1px solid #b8c6d4;color:#333}
.related td a{color:#1a66d6}
.related tfoot td{background:var(--table-foot);height:31px;padding:6px 10px 0 0;text-align:right;border:none}
.pager span{display:inline-block;width:17px;height:17px;background:var(--navy);color:#fff;font-size:10px;line-height:17px;text-align:center;margin-left:1px;border:1px solid #fff}
.pager span.on{background:var(--cyan)}
.big-btn{position:absolute;top:1318px;height:34px;border:1px solid #aaa;border-radius:4px;background:linear-gradient(#fbfbfb,#dedede);color:#888;font-size:16px;line-height:32px;text-align:center;letter-spacing:.5px}
.footer-note{left:138px;top:1421px;font-size:10px;line-height:16px;color:var(--navy)}
.to-top{left:951px;top:1419px;width:131px;height:37px;background:var(--navy);color:#fff;font-size:14px;font-weight:700;line-height:37px;text-align:center;box-shadow:0 2px 0 #9aa8bc}
</style>
</head>
<body>
<div class="stage">
  <div class="abs sheet-shadow"></div>
  <div class="abs sheet-grey"></div>
  <div class="abs sheet"></div>

  <header>
    <div class="abs brand"><span class="brand-dot"></span>Norvale Petrochemical</div>
    <div class="abs site-title">CLEARWAY DESK</div>
    <nav class="abs nav">
      <a style="width:70px;border-color:var(--nav-home)">HOME</a>
      <a style="width:65px;border-color:var(--nav-permits)">PERMITS</a>
      <a style="width:68px;border-color:var(--nav-search)">SEARCH</a>
      <a style="width:67px;border-color:var(--nav-report)">REPORT</a>
      <a style="width:70px;border-color:var(--nav-admin)">ADMIN</a>
      <a style="width:63px;border-color:var(--nav-help)">HELP</a>
    </nav>
    <div class="abs banner" role="img" aria-label="Banner: national emblem, petrochemical plant pipework and an Approved stamp"></div>
  </header>

  <main>
    <div class="abs panel-head">Request Form</div>
    <div class="abs panel-body"></div>

    <svg width="0" height="0" style="position:absolute">
      <defs>
        <symbol id="tile" viewBox="0 0 34 34"><rect width="34" height="34" rx="6" fill="#1d3f73"/><rect x="1.5" y="1.5" width="31" height="31" rx="5" fill="none" stroke="#fff" stroke-opacity=".35"/></symbol>
      </defs>
    </svg>

    <!-- Left column rows: label ends at x=303, icon x=310, colon x=356, field x=367 -->
    <div class="row" style="left:140px;top:365px;width:500px">
      <span class="lbl" style="right:337px">Request Date</span>
      <svg class="ico" style="left:170px"><use href="#tile"/><rect x="9" y="10" width="16" height="14" fill="none" stroke="#fff" stroke-width="2"/><path d="M9 14h16M13 8v4M21 8v4" stroke="#fff" stroke-width="2"/></svg>
      <span class="colon" style="left:214px">:</span>
      <div class="field" style="left:227px;top:3px;width:45px;text-align:center">21</div>
      <div class="field" style="left:280px;top:3px;width:92px">January<i class="caret"></i></div>
      <div class="field" style="left:380px;top:3px;width:57px;text-align:center">2013</div>
    </div>

    <div class="row" style="left:140px;top:409px;width:500px">
      <span class="lbl" style="right:337px">Requester Name</span>
      <svg class="ico" style="left:170px"><use href="#tile"/><rect x="8" y="10" width="18" height="14" rx="2" fill="none" stroke="#fff" stroke-width="2"/><circle cx="14" cy="16" r="2.5" fill="#fff"/><path d="M18 15h5M18 19h5" stroke="#fff" stroke-width="1.6"/></svg>
      <span class="colon" style="left:214px">:</span>
      <div class="field" style="left:227px;top:3px;width:258px">Arun Pello</div>
    </div>

    <div class="row" style="left:140px;top:453px;width:500px">
      <span class="lbl" style="right:337px">Contact No</span>
      <svg class="ico" style="left:170px"><use href="#tile"/><rect x="12" y="7" width="11" height="20" rx="2" fill="none" stroke="#fff" stroke-width="2" transform="rotate(15 17 17)"/><circle cx="17" cy="22" r="1.3" fill="#fff"/></svg>
      <span class="colon" style="left:214px">:</span>
      <div class="field" style="left:227px;top:3px;width:258px">0855 2760 4198</div>
    </div>

    <div class="row" style="left:140px;top:497px;width:500px">
      <span class="lbl" style="right:337px">Company<span class="req">*</span></span>
      <svg class="ico" style="left:170px"><use href="#tile"/><rect x="11" y="8" width="12" height="18" fill="none" stroke="#fff" stroke-width="2"/><path d="M15 11v12M19 11v12" stroke="#fff" stroke-width="2"/></svg>
      <span class="colon" style="left:214px">:</span>
      <div class="field" style="left:227px;top:3px;width:258px">Please select<i class="caret"></i></div>
    </div>

    <div class="row" style="left:140px;top:541px;width:500px">
      <span class="lbl" style="right:337px">Branch<span class="req">*</span></span>
      <svg class="ico" style="left:170px"><use href="#tile"/><rect x="14" y="7" width="6" height="5" fill="#fff"/><rect x="7" y="21" width="6" height="5" fill="#fff"/><rect x="14" y="21" width="6" height="5" fill="#fff"/><rect x="21" y="21" width="6" height="5" fill="#fff"/><path d="M17 12v5M10 21v-4h14v4M17 17v4" stroke="#fff" stroke-width="1.6" fill="none"/></svg>
      <span class="colon" style="left:214px">:</span>
      <div class="field" style="left:227px;top:3px;width:258px">Please select<i class="caret"></i></div>
    </div>

    <div class="row" style="left:140px;top:585px;width:500px">
      <span class="lbl" style="right:337px">Document Category<span class="req">*</span></span>
      <svg class="ico" style="left:170px"><use href="#tile"/><path d="M10 7h11l4 4v16H10z" fill="none" stroke="#fff" stroke-width="2"/><path d="M12 17l3 3 6-7" stroke="#fff" stroke-width="2" fill="none"/></svg>
      <span class="colon" style="left:214px">:</span>
      <div class="field" style="left:227px;top:3px;width:258px">Please select<i class="caret"></i></div>
    </div>

    <div class="row" style="left:140px;top:629px;width:500px">
      <span class="lbl" style="right:337px">Document Type<span class="req">*</span></span>
      <svg class="ico" style="left:170px"><use href="#tile"/><path d="M10 7h11l4 4v16H10z" fill="none" stroke="#fff" stroke-width="2"/><text x="11" y="24" font-size="7" fill="#fff" font-family="sans-serif" font-weight="700">doc</text></svg>
      <span class="colon" style="left:214px">:</span>
      <div class="field" style="left:227px;top:3px;width:258px">Please select<i class="caret"></i></div>
    </div>

    <div class="row" style="left:140px;top:673px;width:500px">
      <span class="lbl" style="right:337px">Expected Use Date<span class="req">*</span></span>
      <svg class="ico" style="left:170px"><use href="#tile"/><rect x="9" y="9" width="16" height="16" rx="2" fill="none" stroke="#fff" stroke-width="2"/><text x="14" y="23" font-size="11" fill="#fff" font-family="sans-serif" font-weight="700">1</text></svg>
      <span class="colon" style="left:214px">:</span>
      <div class="field" style="left:227px;top:3px;width:45px;text-align:center;border-color:#e4e4e4">28</div>
      <div class="field" style="left:280px;top:3px;width:92px;border-color:#e4e4e4">January<i class="caret"></i></div>
      <div class="field" style="left:380px;top:3px;width:57px;text-align:center;border-color:#e4e4e4">2013</div>
    </div>

    <div class="row" style="left:140px;top:717px;width:500px">
      <span class="lbl" style="right:337px">Detail<span class="req">*</span></span>
      <svg class="ico" style="left:170px"><use href="#tile"/><rect x="8" y="9" width="16" height="16" fill="none" stroke="#fff" stroke-width="2"/><path d="M14 19l13-8" stroke="#fff" stroke-width="3"/></svg>
      <span class="colon" style="left:214px">:</span>
      <div class="field area" style="left:227px;top:1px;width:258px">Lorem ipsum dolor sit amet</div>
    </div>

    <div class="row" style="left:140px;top:827px;width:700px">
      <span class="lbl" style="right:537px">Attachment</span>
      <svg class="ico" style="left:170px"><use href="#tile"/><path d="M12 20l8-8a3 3 0 0 1 4 4l-9 9a5 5 0 0 1-7-7l8-8" stroke="#fff" stroke-width="2" fill="none"/></svg>
      <span class="colon" style="left:214px">:</span>
      <div class="field" style="left:227px;top:4px;width:258px">confidential.doc</div>
      <div class="btn" style="left:492px;top:4px;width:73px">BROWSE</div>
      <div class="btn" style="left:574px;top:4px;width:73px">ATTACH</div>
    </div>
    <div class="tag abs" style="left:367px;top:862px;width:77px">file1.doc<b>X</b></div>
    <div class="tag abs" style="left:451px;top:862px;width:78px">file1.doc<b>X</b></div>
    <div class="tag abs" style="left:537px;top:862px;width:77px">file1.doc<b>X</b></div>

    <div class="row" style="left:140px;top:893px;width:500px">
      <span class="lbl" style="right:337px">Coordinator<span class="req">*</span></span>
      <svg class="ico" style="left:170px"><use href="#tile"/><circle cx="17" cy="12" r="4" fill="#fff"/><path d="M9 27c0-6 4-9 8-9s8 3 8 9z" fill="#fff"/><path d="M17 19v6" stroke="#1d3f73" stroke-width="2"/></svg>
      <span class="colon" style="left:214px">:</span>
      <div class="btn" style="left:229px;top:4px;width:72px">ADD</div>
    </div>
    <div class="tag abs" style="left:369px;top:928px;width:110px">Arun Pello HR<b>X</b></div>

    <div class="row" style="left:140px;top:959px;width:500px">
      <span class="lbl" style="right:337px">Related Person<span class="req">*</span></span>
      <svg class="ico" style="left:170px"><use href="#tile"/><circle cx="12" cy="13" r="3.5" fill="#fff"/><circle cx="22" cy="13" r="3.5" fill="#fff"/><path d="M5 25c0-5 3-7 7-7s7 2 7 7zM15 25c0-5 3-7 7-7s7 2 7 7z" fill="#fff"/></svg>
      <span class="colon" style="left:214px">:</span>
      <div class="btn" style="left:229px;top:4px;width:72px;height:23px;line-height:21px">ADD</div>
    </div>
    <div class="tag abs" style="left:369px;top:991px;width:110px">Mira Tan (IT)<b>X</b></div>
    <div class="tag abs" style="left:485px;top:991px;width:131px">Dev Okoro (Finance)<b>X</b></div>
    <div class="tag abs" style="left:369px;top:1012px;width:139px">Lars Venn (Finance)<b>X</b></div>

    <div class="row" style="left:140px;top:1047px;width:500px">
      <span class="lbl" style="right:337px">Remark</span>
      <svg class="ico" style="left:170px"><use href="#tile"/><rect x="7" y="10" width="20" height="12" rx="2" fill="none" stroke="#fff" stroke-width="2"/><path d="M12 22l-2 4 5-4" fill="#fff"/><path d="M11 16h12" stroke="#fff" stroke-width="2" stroke-dasharray="2 1.5"/></svg>
      <span class="colon" style="left:214px">:</span>
      <div class="field area" style="left:227px;top:-3px;width:258px">Lorem ipsum dolor sit amet</div>
    </div>

    <div class="row" style="left:140px;top:1157px;width:230px">
      <span class="lbl" style="right:67px">Related Request</span>
      <svg class="ico" style="left:170px"><use href="#tile"/><ellipse cx="15" cy="15" rx="8" ry="6" fill="#fff"/><ellipse cx="21" cy="19" rx="7" ry="5" fill="none" stroke="#fff" stroke-width="1.6"/><path d="M10 19l-2 5 6-4" fill="#fff"/></svg>
      <span class="colon" style="left:214px">:</span>
    </div>

    <table class="abs related">
      <thead><tr><th style="width:104px">Request No.</th><th style="width:110px">Request Date</th><th style="width:88px">Company</th><th>Branch</th></tr></thead>
      <tbody><tr>
        <td><a>AB56001</a><br><a>BIO5502</a><br><a>AB56001</a><br><a>BIO5502</a></td>
        <td>20/4/2013<br>21/4/2013<br>20/4/2013<br>21/4/2013</td>
        <td>ABC<br>ABC<br>XYZ<br>XYZ</td>
        <td>GC1<br>GC2<br>GC3<br>GC4</td>
      </tr></tbody>
      <tfoot><tr><td colspan="4" class="pager"><span class="on">1</span><span>2</span><span>3</span><span>4</span></td></tr></tfoot>
    </table>

    <div class="big-btn" style="left:366px;width:112px">
      <svg width="40" height="32" style="position:absolute;left:0;top:0"><rect x="0" y="0" width="40" height="32" fill="#e9e9e9"/><path d="M24 9l-7 7 7 7" stroke="#555" stroke-width="2.5" fill="none"/></svg>
      <span style="position:absolute;left:58px">BACK</span>
    </div>
    <div class="big-btn" style="left:488px;width:275px">CREATE NEW REQUEST</div>

    <!-- Right column -->
    <div class="row" style="left:640px;top:365px;width:420px">
      <span class="lbl" style="right:261px">Requester Employee No</span>
      <svg class="ico" style="left:167px"><use href="#tile"/><circle cx="17" cy="17" r="8" fill="none" stroke="#fff" stroke-width="2"/><text x="11.5" y="21" font-size="10" fill="#fff" font-family="sans-serif" font-weight="700">10</text></svg>
      <span class="colon" style="left:211px">:</span>
      <div class="field" style="left:224px;top:3px;width:184px">5520 18764 3011</div>
    </div>
    <div class="row" style="left:640px;top:409px;width:420px">
      <span class="lbl" style="right:261px">Telephone</span>
      <svg class="ico" style="left:167px"><use href="#tile"/><path d="M11 9c-2 2-1 7 4 12s9 6 11 4l-3-4-3 2c-2-1-4-3-5-5l2-3z" fill="#fff"/></svg>
      <span class="colon" style="left:211px">:</span>
      <div class="field" style="left:224px;top:3px;width:184px">3071 2288 615</div>
    </div>
    <div class="abs tooltip">ระหว่างดำเนินการรอดำเนินก ารรอดำเนินการ</div>
  </main>

  <footer>
    <div class="abs footer-note">Copyright © 2013 NorvalePetrochemical. All rights reserved.<br>Terms and Condition | Privacy</div>
    <div class="abs to-top">BACK TO TOP &#708;</div>
  </footer>
</div>
</body>
</html>
```